Call Center In Need of Website Design

We are a call center that provides inbound and outbound calling & marketing services for eCommerce store. We would like to see a fun, creative, playful design that is simple.

Here are some sample design sites we like;
- https://www.velmoreline.com/
- https://pindrask.io/
- https://www.glimbertic.com/live-chat-software/
- https://www.zavrolin.com/

Here are some competitor sites;
- https://www.ostrevaglinks.com/
- https://www.helpkestrel.com/

I have attached website content for your use.

Target Market(s)

eCommerce

Coding

Coded - Design and coding required

Number of Pages Required

5+ page

Font styles to use
Sans Serif

Colors

Designer to choose colors to be used in the design.

Requirements
Must have
• Must have designs for the following 5 separate pages;
• 1. Home (landing)
• - This will be were the design style really needs to show.
• - Just needs to touch on key services
• - CTA
• 2. About Us
• - Basic page for about me paragraph
• 3. Services
• - List of services with icons
• - Click on service type to expand details or hover over service icon to view popup bubble with details about that service
• 4. Pricing
• - Option to bundle 1(one) digital service plan and 1(one) call center service plan
• - Bundling adds 10% monthly discount to over all price
• - Customer does NOT have to bundle
• - FAQ
• 5. Contact Us
• - Include a capture form (name, company name, email, phone, message)
• - Contact info
• - Business hours
• When customer purchases their desired plan, then they are taken to a page where they must schedule a call with an account rep.
Nice to have
• home page animations
Should not have
• All information on Home/Landing page.

```html
<!DOCTYPE html>
<html lang="en">
<head>
<meta charset="utf-8">
<title>Orbitra – Omnichannel Customer Care</title>
<link href="https://fonts.googleapis.com/css2?family=Varela+Round&family=Raleway:wght@400;500;600;700&display=swap" rel="stylesheet">
<style>
:root{
  --space:#383a86;
  --space-deep:#2f3178;
  --lilac:#a9a8d6;
  --mint:#5fc2a6;
  --mint-soft:#7fd8c1;
  --mint-field:#87ddc8;
  --paper:#f7f7f9;
  --ice:#edf5f8;
  --ink:#1f2040;
  --grey:#8a8c99;
  --white:#ffffff;
}
*{box-sizing:border-box;margin:0;padding:0}
html,body{width:768px;height:1200px;overflow:hidden;background:var(--white)}
body{position:relative;font-family:"Raleway",sans-serif;color:var(--ink)}
.abs{position:absolute}
.head{font-family:"Varela Round",sans-serif}

/* hero */
.hero{position:absolute;left:0;top:0;width:768px;height:410px}
.brand{position:absolute;left:104px;top:18px;display:flex;align-items:center;gap:16px}
.brand-dot{width:44px;height:44px;border:3px solid var(--mint);border-radius:50%}
.brand-name{font-family:"Varela Round",sans-serif;font-size:25px;letter-spacing:4px;color:var(--white)}
.nav{position:absolute;top:38px;left:362px;display:flex;gap:0;font-size:7px;font-weight:700;color:var(--white);letter-spacing:.2px}
.nav a{color:inherit;text-decoration:none;position:absolute;white-space:nowrap}
.hero-title{position:absolute;left:103px;top:134px;font-family:"Varela Round",sans-serif;font-size:23px;line-height:27px;color:var(--white)}
.hero-sub{position:absolute;left:103px;top:198px;font-size:12px;color:var(--white);font-weight:500}
.hero-links{position:absolute;left:103px;top:239px;display:flex;gap:14px;font-size:7px;font-weight:700;color:var(--white)}
.hero-links span{border-bottom:2px solid var(--mint);padding-bottom:2px}
.hero-links span.light{border-color:var(--white)}
.vertical-name{position:absolute;left:362px;top:338px;transform:rotate(-90deg);transform-origin:left top;font-family:"Varela Round",sans-serif;font-size:52px;letter-spacing:8px;color:rgba(255,255,255,.14)}
.astronaut{position:absolute;left:520px;top:0;width:248px;height:370px;background:radial-gradient(ellipse at 55% 50%,#6a8fc9 0%,#4a62a8 35%,rgba(56,58,134,0) 70%),linear-gradient(100deg,rgba(56,58,134,0) 60%,#b9c3ec 85%,rgba(56,58,134,0) 100%)}

/* what we do */
.services-band{position:absolute;left:0;top:360px;width:768px;height:238px;background:var(--paper);z-index:-1}
.card{position:absolute;top:425px;width:120px;height:129px;background:var(--white);box-shadow:0 2px 6px rgba(0,0,0,.08)}
.card-top{height:72px;background:var(--space);display:flex;align-items:center;justify-content:center}
.card-title{margin:13px 0 0 10px;font-size:7.5px;font-weight:600}
.card-title:before{content:"•";margin-right:5px}
.card-list{margin:6px 0 0 10px;font-size:6px;line-height:10px;color:var(--grey)}
.wwd-title{position:absolute;left:384px;top:426px;font-size:11px;font-weight:700}
.rule{position:absolute;height:1.5px;width:20px;background:var(--ink)}
.wwd-text{position:absolute;left:384px;top:463px;width:285px;font-size:6.4px;line-height:12.5px;color:#55576a}
.btn-more{position:absolute;left:384px;top:529px;width:62px;height:24px;border-radius:12px;background:var(--mint);color:var(--white);font-size:7px;font-weight:700;display:flex;align-items:center;justify-content:center}

/* faq */
.faq-band{position:absolute;left:0;top:598px;width:768px;height:320px;background:var(--ice);z-index:-1}
.faq-title{position:absolute;left:0;width:768px;top:634px;text-align:center;font-family:"Varela Round",sans-serif;font-size:19px;color:var(--space-deep);font-weight:700}
.faq-sub{position:absolute;left:0;width:768px;top:681px;text-align:center;font-size:7px;color:#45475a}
.faq-card{position:absolute;left:144px;top:715px;width:480px;height:122px;background:var(--white);box-shadow:0 2px 8px rgba(0,0,0,.08)}
.quote-mark{position:absolute;left:0;top:-20px;font-family:"Varela Round",sans-serif;font-size:120px;color:#eeeef2;line-height:1}
.faq-answer{position:absolute;left:77px;top:22px;width:370px;font-size:6.6px;line-height:12.5px;color:#45475a}
.faq-question{position:absolute;left:77px;top:82px;font-size:7.5px;font-weight:500}
.faq-brand{position:absolute;left:277px;top:61px;display:flex;align-items:center;gap:12px}
.faq-brand .brand-dot{width:34px;height:34px;border-width:2px}
.faq-brand .brand-name{color:#3f4152;font-size:19px;letter-spacing:3px}
.dots{position:absolute;left:362px;top:857px;display:flex;gap:5px;align-items:center}
.dots i{width:3.5px;height:3.5px;border-radius:50%;background:var(--ink)}
.dots i.on{width:6px;height:6px;background:var(--mint)}
.moon-astronaut{position:absolute;left:8px;top:822px;width:142px;height:92px;border-radius:40% 40% 10% 10%;background:radial-gradient(ellipse at 50% 70%,#e6e8ec 0%,#cfd3da 45%,rgba(237,245,248,0) 75%)}

/* call back */
.callback{position:absolute;left:0;top:895px;width:768px;height:240px}
.contact-box{position:absolute;left:120px;top:952px;width:175px;height:150px;background:var(--mint-soft)}
.contact-box h3{position:absolute;left:14px;top:22px;font-size:10px;font-weight:700;color:var(--white)}
.contact-box .rule{left:14px;top:43px;background:var(--white)}
.contact-line{position:absolute;left:14px;display:flex;gap:7px;font-size:7px;line-height:12px;color:var(--white)}
.cb-title{position:absolute;left:312px;top:950px;font-family:"Varela Round",sans-serif;font-size:19px;font-weight:700;color:var(--white)}
.field{position:absolute;width:162px;height:24px;background:var(--mint-field);border:1px solid rgba(255,255,255,.45);font-size:6.5px;color:var(--white);padding:9px 9px;font-weight:500}
.submit{position:absolute;left:312px;top:1071px;width:67px;height:24px;border:1.5px solid var(--white);border-radius:3px;color:var(--white);font-size:7px;font-weight:700;display:flex;align-items:center;justify-content:center}

/* footer */
.copyright{position:absolute;left:103px;top:1154px;font-size:7px;line-height:13px;color:var(--grey)}
.foot-nav{position:absolute;top:1163px;font-size:7.5px;color:#5d5f6e}
.foot-nav.active{color:var(--mint)}
.social{position:absolute;top:1159px;width:17px;height:17px;border-radius:2px}
</style>
</head>
<body>

<svg class="hero" viewBox="0 0 768 410" aria-hidden="true">
  <path d="M0 0H768V330C700 370 620 400 540 398C440 396 380 360 300 352C200 342 120 372 0 362Z" fill="var(--space)"/>
  <path d="M300 352C380 360 440 396 540 398C620 400 700 370 768 330V342C700 384 620 410 540 404C440 400 380 366 300 352Z" fill="var(--lilac)" opacity=".7"/>
</svg>

<div class="astronaut" role="img" aria-label="Illustration of an astronaut floating beside a glowing comet trail"></div>
<div class="vertical-name" aria-hidden="true">ORBITRA</div>

<header class="brand">
  <span class="brand-dot"></span>
  <span class="brand-name">ORBITRA</span>
</header>
<nav class="nav">
  <a style="left:0">HOME</a>
  <a style="left:43px">ABOUT US</a>
  <a style="left:98px">SERVICES</a>
  <a style="left:152px">PRICING</a>
  <a style="left:203px">CONTACT US</a>
  <a style="left:269px">ACCOUNT</a>
</nav>

<h1 class="hero-title">Orbitra Is An<br>Omnichannel</h1>
<p class="hero-sub">Provider For Customer Care</p>
<div class="hero-links"><span>LEARN MORE</span><span class="light">GET STARTED</span></div>

<div class="services-band"></div>

<article class="card" style="left:110px">
  <div class="card-top">
    <svg width="54" height="46" viewBox="0 0 54 46" fill="none" stroke="#fff" stroke-width="2.2">
      <rect x="8" y="10" width="38" height="24" rx="2"/>
      <path d="M3 36H51L48 40H6Z" fill="#fff"/>
      <circle cx="24" cy="14" r="7"/>
      <path d="M27 18L36 28" stroke-width="3"/>
    </svg>
  </div>
  <p class="card-title">Digital Services</p>
  <p class="card-list">Email Support<br>Live Chat Support</p>
</article>

<article class="card" style="left:240px">
  <div class="card-top">
    <svg width="50" height="50" viewBox="0 0 50 50" fill="none" stroke="#fff" stroke-width="2.4">
      <circle cx="25" cy="20" r="11" fill="#fff"/>
      <path d="M11 22C11 10 18 5 25 5S39 10 39 22"/>
      <path d="M6 46C8 36 16 32 25 32S42 36 44 46Z" fill="#fff"/>
      <circle cx="30" cy="41" r="2.5" fill="var(--space)" stroke="#fff"/>
    </svg>
  </div>
  <p class="card-title">Call Center Services</p>
  <p class="card-list">Answering service<br>Welcome Calls</p>
</article>

<h2 class="wwd-title">What We Do</h2>
<span class="rule" style="left:384px;top:448px"></span>
<p class="wwd-text">Orbitra is your personal customer service and product research team. We love eCommerce, but we love seeing business owners succeed even more! That is exactly why we have developed the processes and technology to take care of the most over looked areas in eCommerce - Customer Service and Retention.</p>
<div class="btn-more">More</div>

<div class="faq-band"></div>
<h2 class="faq-title">Frequently Asked Quetions</h2>
<span class="rule" style="left:373px;top:663px;background:var(--space-deep)"></span>
<p class="faq-sub">Lorem Ipsum Dolor Sit Amet Consectetor Lorem Ipsum Dolor Sit Amet Consectetor</p>

<section class="faq-card">
  <span class="quote-mark" aria-hidden="true">“</span>
  <p class="faq-answer">The free trial only relates to the "call center" service packages! There is no hidden fine print or fees to get started. We don't even require any payment info, signatures, or deposits. If you don't like us or our service, just simply walk away.</p>
  <p class="faq-question">Is the free trial really free?</p>
  <div class="faq-brand"><span class="brand-dot"></span><span class="brand-name">ORBITRA</span></div>
</section>

<svg class="abs" style="left:148px;top:850px" width="468" height="14" viewBox="0 0 468 14" fill="none" stroke="#7a7c88" stroke-width="1.4">
  <path d="M2 7H15M2 7L6 3M2 7L6 11"/>
  <path d="M466 7H453M466 7L462 3M466 7L462 11"/>
</svg>
<div class="dots"><i class="on"></i><i></i><i></i><i></i><i></i></div>

<svg class="callback" viewBox="0 0 768 240" aria-hidden="true">
  <path d="M0 14C40 8 70 16 110 12S180 6 220 12S300 16 340 10S420 8 460 13S540 16 580 10S660 8 700 13S750 12 768 10V240H0Z" fill="var(--mint)"/>
</svg>
<div class="moon-astronaut" role="img" aria-label="Illustration of an astronaut resting on the moon with a flag"></div>

<aside class="contact-box">
  <h3>Contact Details</h3>
  <span class="rule"></span>
  <div class="contact-line" style="top:58px">
    <svg width="9" height="9" viewBox="0 0 10 10"><path d="M2 1L4 3L3 4.5C3.8 6 4.5 6.7 5.5 7L7 6L9 8L7.5 9.5C4 9 1 6 .5 2.5Z" fill="#fff"/></svg>
    <span>Phone: (800) 555-0147</span>
  </div>
  <div class="contact-line" style="top:76px">
    <svg width="9" height="9" viewBox="0 0 10 10"><rect x=".5" y="2" width="9" height="6.5" fill="#fff"/><path d="M.5 2L5 5.5L9.5 2" stroke="var(--mint-soft)" fill="none"/></svg>
    <span>hello@orbitra.example</span>
  </div>
  <div class="contact-line" style="top:94px">
    <svg width="9" height="10" viewBox="0 0 10 12"><path d="M5 11C5 11 1 6.5 1 4.5A4 4 0 0 1 9 4.5C9 6.5 5 11 5 11Z" fill="#fff"/><circle cx="5" cy="4.5" r="1.4" fill="var(--mint-soft)"/></svg>
    <span>Orbitra, Inc.<br>418 Lanterly Ave. Corvane, CA 90000</span>
  </div>
</aside>

<h2 class="cb-title">Request For Call Back</h2>
<div class="field" style="left:312px;top:999px">Name</div>
<div class="field" style="left:485px;top:999px">Email</div>
<div class="field" style="left:312px;top:1033px">Ph Num</div>
<div class="field" style="left:485px;top:1033px">Enquiry About</div>
<div class="submit">Submit Now</div>

<footer>
  <p class="copyright">Copyright © 2018.<br>All rights reserved.</p>
  <span class="foot-nav active" style="left:263px">Home</span>
  <span class="foot-nav" style="left:305px">About Us</span>
  <span class="foot-nav" style="left:357px">Service</span>
  <span class="foot-nav" style="left:401px">Pricing</span>
  <span class="foot-nav" style="left:445px">Contact Us</span>
  <span class="foot-nav" style="left:503px">Account</span>
  <span class="social" style="left:588px;background:var(--mint)"></span>
  <span class="social" style="left:608px;background:var(--space)"></span>
  <span class="social" style="left:628px;background:var(--lilac)"></span>
  <span class="social" style="left:648px;background:var(--space-deep)"></span>
</footer>

</body>
</html>
```